Webdesign für freie Trauungen
Zielgruppe
Webseite für Hochzeitspaare, Trauerende, Bestatter, Interessierte
Aufgabenstellung
Internetseite
Briefing:
Onepager
Internetseite soll wirken:
Modern
Schlank
Klar
Vertrauenserweckend
professionell
Home:
Reden für besondere Momente im Leben
Schrift an Flyer anpassen
REDEN.
ERZÄHLEN.
ERINNERN.
BERÜHREN.
Bild von mir,
Dazu, meine Reden sind:
freundlich
authentisch
ehrlich
einfühlsam
taktvoll
humorvoll
tiefsinnig
tröstend
nett
zugewandt
interessant
nach Euren Wünschen
mit Euren Inhalten
individuell
sehr persönlich
kreativ
wortgewandt
erfahren
Sprechen Sie mich an! ?
FREIE TRAUUNG:
EINFACH HIMMLISCH!
eine Liebesgeschichte erzählen
Sich ein Versprechen geben
JA zueinander sagen
Mit lieben Menschen feiern
wo, wann, wie - das entscheidet Ihr!
Segensfeier - Willkommensfeier:
im Leben willkommen heißen
Was bedeutet der Name des Kindes?
Was wollt Ihr Eurem Kind mitgeben?
Was wünscht Ihr Euch für Euer Kind?
TRAUERFEIER:
an schöne Momente erinnern
Einen Menschen mit Worten lebendig werden lassen
Mit einer persönlichen und bewegenden Ansprache
Mit all dem, was Sie sich wünschen!
REDEN ZU GEBURTSTAGEN:
mit Humor, Witz und Verstand gemeinsam zurück schauen
Und von Träumen und Sehnsüchten erzählen
Reden zum Jubiläum:
gemeinsam zurück schauen
Geleistetes würdigen
Veränderungen verständlich machen
Ausblicke wagen
Biographien:
festhalten, damit nichts von Ihrer Lebensgeschichte verloren geht
Sie erinnern sich und ich schreibe auf
Referenzen:
???? Wie am besten ???
Persönliches Vita:
Studium an der Hohen Akademie Tellbrück:
- Publizistik
Germanistik
Volkswirtschaftslehre
Lateinamerikanistik
Abschluß: Magistra Artium
Freie Rednerin seit 1998
Telefonnummer 015923847261
Email: marlies.Kersten@postfeld.de
Wirk..

```html
<!DOCTYPE html>
<html lang="de">
<head>
<meta charset="utf-8">
<title>Kersten Reden</title>
<link rel="stylesheet" href="https://fonts.googleapis.com/css2?family=Source+Sans+3:ital,wght@0,300;0,400;0,600;1,400;1,600&display=swap">
<style>
:root{
  --accent:#6a9994;
  --accent-soft:#a9c4c0;
  --text:#555b5a;
  --heading:#4a4f4f;
  --muted:#8a8f8e;
  --panel:#f2f4f3;
  --white:#ffffff;
  --footer:#333535;
}
*{margin:0;padding:0;box-sizing:border-box}
html,body{width:1200px;height:4231px;overflow:hidden}
body{font-family:"Source Sans 3",sans-serif;color:var(--text);background:var(--white);position:relative}
.abs{position:absolute}
.ph{position:absolute}
/* header */
.site-header{position:absolute;top:0;left:0;width:1200px;height:86px;background:var(--white)}
.brand{position:absolute;left:54px;top:18px;font-size:30px;font-weight:400;color:var(--heading);letter-spacing:1px;line-height:1}
.brand small{display:block;font-size:13px;letter-spacing:9px;margin-top:4px}
.main-nav{position:absolute;right:54px;top:36px;display:flex;gap:34px;font-size:11px;letter-spacing:.3px;color:var(--heading)}
.main-nav .active{color:var(--accent)}
/* hero */
.hero{position:absolute;top:86px;left:0;width:1200px;height:500px;background:var(--panel)}
.hero-photo{left:450px;top:0;width:750px;height:500px;background:linear-gradient(90deg,#5f6562 0%,#9b9a93 30%,#5b5550 50%,#a49c8f 75%,#6e6660 100%)}
.hero-title{position:absolute;left:136px;top:124px;font-size:37px;font-weight:300;line-height:44px;color:var(--heading);letter-spacing:1px}
.hero-sub{position:absolute;left:136px;top:332px;font-size:16px;line-height:21px;color:var(--accent)}
/* about */
.about{position:absolute;top:586px;left:0;width:1200px;height:616px}
.about-circle{left:124px;top:737px;width:388px;height:388px;border-radius:50%;background:var(--accent-soft)}
.about-photo{left:186px;top:681px;width:264px;height:444px;border-radius:40% 40% 50% 50%/20% 20% 30% 30%;background:linear-gradient(180deg,#e8d7a8 0%,#b7aea2 35%,#f2efe9 75%,#d7d2cb 100%)}
.section-title{font-size:27px;font-weight:300;color:var(--heading);letter-spacing:.5px;text-align:center}
.cloud span{position:absolute;white-space:nowrap;color:var(--text)}
.btn{position:absolute;background:var(--accent);color:var(--white);font-size:10px;font-weight:600;letter-spacing:.4px;display:flex;align-items:center;justify-content:center}
/* offers */
.offers{position:absolute;top:1202px;left:0;width:1200px;height:2045px;background:var(--panel)}
.card{position:absolute;width:444px;height:561px;background:var(--white);box-shadow:0 10px 30px rgba(0,0,0,.07)}
.card-icon{position:absolute;left:45px;top:-10px;width:32px;height:31px;background:var(--accent)}
.card-img{position:absolute;left:45px;top:46px;width:356px;height:236px}
.card h3{position:absolute;left:45px;top:320px;font-size:21px;font-weight:400;line-height:28px;color:var(--accent);letter-spacing:.3px}
.card p{position:absolute;left:45px;font-size:16px;line-height:21px;font-weight:300;color:var(--text)}
/* vita */
.vita{position:absolute;top:3247px;left:0;width:1200px;height:562px}
.vita h4{font-size:16px;font-weight:400;color:var(--accent);line-height:20px}
.vita ul{font-size:12px;color:var(--muted);line-height:18px;padding-left:16px}
.contact-box{left:386px;top:3410px;width:221px;height:284px;background:var(--panel)}
.vita-photo{left:637px;top:3410px;width:427px;height:284px;background:linear-gradient(135deg,#3f5a4d 0%,#d8cdb8 45%,#e9e0cf 60%,#2f4a3f 100%)}
/* testimonials */
.testimonials{position:absolute;top:3809px;left:0;width:1200px;height:364px;background:linear-gradient(180deg,#eef1f0,#fafbfb)}
.avatar{left:561px;top:3940px;width:76px;height:76px;border-radius:50%;background:radial-gradient(circle,#e7cfae,#c9a98a)}
.quote{position:absolute;left:300px;top:4036px;width:600px;text-align:center;font-size:12px;line-height:16px;color:var(--muted)}
.dot{position:absolute;top:4116px;width:10px;height:10px;border-radius:50%;background:#dcdfde}
/* footer */
.site-footer{position:absolute;top:4173px;left:0;width:1200px;height:58px;background:var(--footer);color:#e6e6e6}
.site-footer .brand{color:#e6e6e6;top:12px;font-size:22px}
.site-footer .brand small{font-size:10px;letter-spacing:6px;margin-top:2px}
.footer-nav{position:absolute;left:440px;top:23px;display:flex;gap:28px;font-size:10px;letter-spacing:.3px}
.copyright{position:absolute;right:54px;top:23px;font-size:10px;letter-spacing:.3px}
</style>
</head>
<body>

<header class="site-header">
  <div class="brand">Kersten<small>REDEN</small></div>
  <nav class="main-nav">
    <span class="active">START</span><span>MEINE REDEN</span><span>WAS ICH ANBIETE</span><span>PERSÖNLICHES VITA</span><span>REFERENZEN</span>
  </nav>
</header>

<section class="hero">
  <div class="ph hero-photo" role="img" aria-label="Porträtfoto der Rednerin in Lederjacke vor einer Glasscheibe"></div>
  <h1 class="hero-title">REDEN.<br>ERZÄHLEN.<br>ERINNERN.<br>BERÜHREN.</h1>
  <p class="hero-sub">REDEN FÜR BESONDERE<br>MOMENTE IM LEBEN</p>
</section>

<section class="about">
</section>
<div class="ph about-circle"></div>
<div class="ph about-photo" role="img" aria-label="Foto der Rednerin im grauen Blazer"></div>
<h2 class="abs section-title" style="left:634px;top:700px;width:400px">MEINE REDEN SIND</h2>
<div class="cloud">
  <span style="left:770px;top:796px;font-size:13px;font-style:italic;font-weight:600">taktvoll</span>
  <span style="left:847px;top:796px;font-size:13px">interessant</span>
  <span style="left:681px;top:823px;font-size:26px;font-weight:600">authentisch</span>
  <span style="left:843px;top:829px;font-size:21px">erfahren</span>
  <span style="left:956px;top:833px;font-size:18px;font-style:italic">tiefsinnig</span>
  <span style="left:680px;top:880px;font-size:12px">nett</span>
  <span style="left:746px;top:869px;font-size:22px">einfühlsam</span>
  <span style="left:895px;top:864px;font-size:27px;font-style:italic;font-weight:600">humorvoll</span>
  <span style="left:590px;top:912px;font-size:21px;font-style:italic;font-weight:600">zugewandt</span>
  <span style="left:723px;top:905px;font-size:28px">nach Euren Wünschen</span>
  <span style="left:686px;top:955px;font-size:22px;font-style:italic">sehrpersönlich</span>
  <span style="left:875px;top:957px;font-size:21px;font-weight:600">mit Euren Inhalten</span>
  <span style="left:716px;top:999px;font-size:15px;font-weight:600">ehrlich</span>
  <span style="left:810px;top:999px;font-size:15px">individuell</span>
  <span style="left:600px;top:890px;font-size:18px;transform:rotate(-90deg);transform-origin:left top">kreativ</span>
  <span style="left:640px;top:890px;font-size:12px;font-style:italic;transform:rotate(-90deg);transform-origin:left top">wortgewandt</span>
  <span style="left:1038px;top:940px;font-size:15px;transform:rotate(-90deg);transform-origin:left top">freundlich</span>
  <span style="left:1074px;top:975px;font-size:15px;font-style:italic;font-weight:600;transform:rotate(-90deg);transform-origin:left top">tröstend</span>
</div>
<div class="btn" style="left:750px;top:1065px;width:166px;height:30px">SPRECHEN SIE MICH AN!</div>

<section class="offers">
  <h2 class="abs section-title" style="left:400px;top:83px;width:400px">WAS ICH ANBIETE</h2>

  <article class="card" style="left:136px;top:192px">
    <div class="card-icon"></div>
    <div class="card-img" role="img" aria-label="Foto eines Brautpaars beim Auszug unter Konfetti" style="background:linear-gradient(135deg,#3c3a36,#9b968d 50%,#e4e1da 70%,#4a4640)"></div>
    <h3>FREIE TRAUUNG:<br>EINFACH HIMMLISCH!</h3>
    <p style="top:403px">eine Liebesgeschichte erzählen<br>Sich ein Versprechen geben<br>JA zueinander sagen<br>Mit lieben Menschen feiern</p>
    <p style="top:508px">wo, wann, wie – das entscheidet Ihr!</p>
  </article>

  <article class="card" style="left:620px;top:192px">
    <div class="card-icon"></div>
    <div class="card-img" role="img" aria-label="Foto einer Mutter mit lachendem Baby" style="background:linear-gradient(135deg,#5c5448,#b39a82 45%,#e2d7c9 65%,#7d7466)"></div>
    <h3>SEGENSFEIER<br>WILLKOMMENSFEIER</h3>
    <p style="top:403px">im Leben willkommen heißen<br>Was bedeutet der Name des Kindes?<br>Was wollt Ihr Eurem Kind mitgeben?<br>Was wünscht Ihr Euch für Euer Kind?</p>
  </article>

  <article class="card" style="left:136px;top:799px">
    <div class="card-icon"></div>
    <div class="card-img" role="img" aria-label="Foto weißer Blumen und einer brennenden Kerze" style="background:linear-gradient(135deg,#1e1e1f,#5e5c5a 40%,#c9c6c0 55%,#2a2827)"></div>
    <h3>TRAUERFEIER</h3>
    <p style="top:375px">an schöne Momente erinnern<br>Einen Menschen mit Worten<br>lebendig werden lassen<br>Mit einer persönlichen und<br>bewegenden Ansprache</p>
    <p style="top:498px">Mit all dem, was Sie sich wünschen!</p>
  </article>

  <article class="card" style="left:620px;top:799px">
    <div class="card-icon"></div>
    <div class="card-img" role="img" aria-label="Foto einer Geburtstagsfeier im Garten" style="background:linear-gradient(135deg,#5b6a52,#a9a48c 45%,#d9cfc0 65%,#6d6a58)"></div>
    <h3>REDEN ZU GEBURTSTAGEN</h3>
    <p style="top:375px">mit Humor, Witz und Verstand<br>gemeinsam zurück schauen<br>Und von Träumen und Sehnsüchten<br>erzählen</p>
  </article>

  <article class="card" style="left:136px;top:1406px">
    <div class="card-icon"></div>
    <div class="card-img" role="img" aria-label="Foto einer feiernden Gruppe beim Anstoßen" style="background:linear-gradient(135deg,#2f3a45,#7b8793 45%,#c8c3bb 60%,#3a3f48)"></div>
    <h3>REDEN ZUM JUBILÄUM</h3>
    <p style="top:375px">gemeinsam zurück schauen<br>Geleistetes würdigen<br>Veränderungen verständlich machen<br>Ausblicke wagen</p>
  </article>

  <article class="card" style="left:620px;top:1406px">
    <div class="card-icon"></div>
    <div class="card-img" role="img" aria-label="Foto einer alten Schreibmaschine auf Holztisch" style="background:linear-gradient(135deg,#4a3526,#8a6a4f 40%,#6b5240 60%,#3a2a1f)"></div>
    <h3>BIOGRAPHIEN</h3>
    <p style="top:375px">festhalten, damit nichts von Ihrer<br>Lebensgeschichte verloren geht<br>Sie erinnern sich und ich schreibe auf</p>
  </article>
</section>

<section class="vita">
  <h2 class="abs section-title" style="left:136px;top:68px;text-align:left;font-size:29px">PERSÖNLICHES VITA</h2>
  <div class="abs" style="left:136px;top:170px;width:220px">
    <h4>STUDIUM AN DER HOHEN<br>AKADEMIE TELLBRÜCK</h4>
    <ul style="margin-top:8px"><li>Publizistik</li><li>Germanistik</li><li>Volkswirtschaftslehre</li><li>Lateinamerikanistik</li><li>Abschluß: Magistra Artium</li></ul>
    <h4 style="margin-top:20px">FREIE REDNERIN SEIT 1998</h4>
    <h4 style="margin-top:28px">WIRKUNGSKREIS</h4>
    <p style="font-size:12px;line-height:18px;color:var(--muted);margin-top:8px">Aachen, Viersen, Düsseldorf,<br>Krefeld, Erkelenz, Neuss, Köln</p>
  </div>
</section>
<div class="ph contact-box">
  <h4 style="position:absolute;left:37px;top:102px;font-size:16px;font-weight:400;color:var(--accent)">KONTAKT</h4>
  <p style="position:absolute;left:37px;top:137px;font-size:12px;line-height:27px;color:var(--heading)">marlies.kersten@postfeld.de<br>0159-23847261<br><span style="color:var(--accent)">kerstenreden.de</span></p>
</div>
<div class="ph vita-photo" role="img" aria-label="Porträtfoto der Rednerin mit Brille auf grünem Sessel"></div>
<div class="btn" style="left:898px;top:3715px;width:166px;height:31px">SPRECHEN SIE MICH AN!</div>

<section class="testimonials">
  <h2 class="abs section-title" style="left:300px;top:69px;width:600px">DAS SAGEN KUNDEN ÜBER MICH</h2>
</section>
<div class="ph avatar" role="img" aria-label="Kundenporträt"></div>
<p class="quote">Sed eiusmod tempor incidunt ut labore et dolore magna aliqua. Ut enim ad minim veniam, quis nostrud exercitation ullamco laboris nisi ut aliquid ex ea commodi consequat.<br><span style="display:block;margin-top:10px;color:var(--heading)">Miriam Musterfrau</span></p>
<span class="dot" style="left:580px;background:var(--accent)"></span>
<span class="dot" style="left:595px"></span>
<span class="dot" style="left:610px"></span>

<footer class="site-footer">
  <div class="brand">Kersten<small>REDEN</small></div>
  <nav class="footer-nav"><span>STARTSEITE</span><span>KONTAKT</span><span>IMPRESSUM</span><span>DATENSCHUTZ</span></nav>
  <div class="copyright">COPYRIGHT @2021 MARLIES KERSTEN</div>
</footer>

</body>
</html>
```